Web Design Project for a Software & Consulting Company

We have just completed a recent ArtHerdly project for a new logo (see attached).
As the next stage of our rebranding we now require a website re-design to complement the new logo.
Our current site, http://www.corvinsoft.example was built in-house and does not come across as professional as we would like. We supply software and associated services to some of the world’s largest oil companies and we need our site to reflect that level of client.
We will also be posting another design project for brochures, PowerPoint slides and other materials very soon.
We would like designs for…
Home page
Product page
• TZQ
• BLV
• PNJ
Services
News page
About Us page
Contact Us page
Page for mobile devices that gives basic company and product information
Currently the site is small but we intend to increase content to include white papers etc. this should be taken into account when designing the navigation therefore we would prefer navigation through styled text links rather than images.
Colour schemes should broadly be taken from our new logo, where the dark blue and dark green from the left and right sides of the logo are the main colours, but other, brighter accent colours can be used to highlight sections or content.
Dark Blue = C:88, M:55, Y:44, K:28
Dark Green = C:87, M:53, Y:50, K:50
NB: Don’t use the logo on our current site, make sure you use the one attached.
We would prefer the final file format to be a layered PSD.
The site should be clean and professional and communicate the following...
• That we have a great depth and breadth of knowledge about our customers’ business, enabling us to deliver the best systems and solutions.
• That we are a leading provider of cost estimation and control solutions to the oil and gas industry.
• The benefits of our software and consulting services.
• Show that we deliver outstanding customer service and value with a very high level of professionalism
• The site should have no Flash and be able to self-adjust to fit any screen size.
Things to avoid …
• Obvious and clichéd oil industry imagery, no oil rigs
• Cartoon style graphics
Our Background
We are an integrated software and consulting organization specialising in the drilling side of the oil and gas industry. Simply put our software helps companies better understand, predict and communicate the cost of drilling wells.
We have 3 software products and a consulting offering consisting of…
• TZQ - Probabilistic time and cost software
• BLV – Cost tracking and reporting software
• PNJ – (currently known as DrillSavant) – Lessons learned software
• Consulting services
Our systems are in use in over 30 countries with a broad range of clients including: GN, Marovel, Dunt, Koruna, VELO Sirkami, FALUMI and Quintex.
Our current site can be found at www.corvinsoft.example
Our main competitors are
• http://www.drovanic.example/
• http://www.sumbrask.example/
• http://www.kve.example/services/software-solutions/p1-
Our depth of drilling knowledge, quality of software and collaboration with clients differentiate us form the competition.
We strive for very high levels of customer service.
We look forward to receiving your designs!
Updates
Thanks to all the designers who have submitted a design, we appreciate the effort.
We will do our best to give individual feedback on each design but given that many are quite similar we thought we would give some general feedback first.
Nearly all the designs submitted so far have been slight variations on…
-
Top Menu
-
Scrolling Photo Banner
-
4 Columns
-
Body
-
Deep Footer
These designs are well executed but they are basically the same layout as our existing site and while there is nothing inherently wrong with this layout we would like to see some designs that are a bit more innovative and different. We don’t really want just a polished version of our current site.
Thanks again,
CVS
Thanks to everyone who has submitted a design, the response has been great.
We are close to making a decision so if you are intending to submit a design please do it soon, the deadline is only a few days away.
Thanks again.
CVS
Target Market(s)
Mid to high level executives
Industry/Entity Type
Oil And Gas
Look and feel

```html
<!DOCTYPE html>
<html lang="en">
<head>
<meta charset="utf-8">
<title>Corvin Software</title>
<link href="https://fonts.googleapis.com/css2?family=Ubuntu:ital,wght@0,400;0,500;0,700;1,400&display=swap" rel="stylesheet">
<style>
:root{
  --teal-dark:#1d5365;
  --teal:#24667a;
  --teal-tab:#1f5e6e;
  --ink:#2b3438;
  --ink-soft:#4a4f52;
  --red:#b3262a;
  --green-top:#9ccc2a;
  --green-bot:#3d7a0c;
  --footer:#414141;
  --footer-text:#d9d9d9;
  --panel:#ffffff;
}
*{box-sizing:border-box;margin:0;padding:0}
html,body{width:847px;height:1200px;overflow:hidden}
body{font-family:"Ubuntu",sans-serif;background:var(--teal-dark);position:relative;color:var(--ink)}
.abs{position:absolute}
.header{left:0;top:0;width:847px;height:115px;background:linear-gradient(#ffffff,#e6e8e9);border-bottom:1px solid #9fb0b6}
.logo{left:92px;top:44px;display:flex;align-items:center;gap:9px;color:var(--teal-dark);font-weight:700;font-size:17px;letter-spacing:1px}
.logo .mark{width:30px;height:30px;border-radius:50%;background:var(--teal-dark)}
.search{left:600px;top:37px;width:155px;height:21px;border:1px solid #b9bcbd;border-radius:3px;background:#fff;font-size:8px;font-style:italic;color:#8a8a8a;padding:5px 6px}
.search .btn{position:absolute;right:-1px;top:-1px;width:31px;height:21px;background:linear-gradient(#9aa57b,#6e7a4e);border-radius:0 3px 3px 0}
.search .btn svg{position:absolute;left:9px;top:4px}
.nav{top:89px;left:400px;display:flex;font-size:10.5px;color:var(--ink)}
.nav a{display:block;height:26px;line-height:26px;padding:0 7px;margin-left:6px;text-decoration:none;color:inherit}
.nav a.active{background:var(--teal-tab);color:#fff;font-weight:500;border-radius:5px 5px 0 0}
.hero{left:92px;top:117px;width:663px;height:326px;border:2px solid #dfe3e4;
  background:
    linear-gradient(180deg,rgba(255,255,255,0) 70%,rgba(240,238,232,.5) 100%),
    radial-gradient(ellipse 180px 120px at 78% 78%,#1b1f24 0%,rgba(27,31,36,0) 100%),
    linear-gradient(100deg,#eeece8 0%,#d7d8d6 30%,#9aa6b0 55%,#5c6b7a 75%,#2f3b48 100%)}
.hero h1{position:absolute;left:27px;top:115px;width:385px;font-size:25.5px;line-height:31px;font-weight:500;color:#1c2226}
.arrow{top:241px;width:55px;height:70px;background:rgba(40,40,40,.55)}
.arrow svg{position:absolute;left:20px;top:23px}
.dropdown{left:454px;top:115px;width:104px;height:75px;background:var(--teal-tab);font-size:8.5px;color:#e3eef1}
.dropdown li{list-style:none;height:22px;line-height:22px;padding-left:23px;border-bottom:1px solid #2f7587;position:relative}
.dropdown li:last-child{border-bottom:0}
.dropdown li:before{content:"";position:absolute;left:10px;top:10px;width:2px;height:2px;background:#e3eef1}
.news{left:92px;top:465px;width:663px;height:52px;background:#fff;border-radius:6px;display:flex;align-items:center}
.news .label{width:137px;height:40px;border-right:1px solid #d7d7d7;display:flex;align-items:center;gap:8px;padding-left:10px;font-size:13px;font-weight:500}
.news .ico{width:32px;height:32px;border-radius:4px;background:linear-gradient(#f4f4f4,#aab0b3);border:1px solid #9ca3a6}
.news .body{padding-left:9px;width:430px}
.news .body b{font-size:9px;font-weight:500;display:block;margin-bottom:3px}
.news .body i{font-size:7.5px;color:#666;line-height:11px;display:block}
.news .more{margin-left:30px;font-size:8.5px;font-weight:700;text-decoration:underline;display:flex;align-items:center;gap:5px}
.news .more span{width:15px;height:15px;border-radius:50%;border:1px solid #999;font-size:9px;text-align:center;line-height:12px;color:#666;text-decoration:none;display:inline-block}
.panel{left:92px;top:525px;width:663px;height:480px;background:var(--panel);border-radius:6px}
.card{width:313px;height:110px;background:linear-gradient(#fafafa,#ececec);border:1px solid #d5d5d5;border-radius:2px}
.card .pic{position:absolute;left:13px;top:13px;width:85px;height:83px;border:2px solid #c3d2d6;background:radial-gradient(circle at 50% 45%,#5aa9c4 0%,#2a7896 55%,#17536b 100%)}
.card h2{position:absolute;left:112px;top:11px;font-size:12px;font-weight:500;color:var(--teal-dark)}
.card h2 span{color:var(--red);font-size:10px}
.card p{position:absolute;left:112px;top:29px;width:188px;font-size:8.5px;line-height:14px;color:var(--ink-soft)}
.btn-more{position:absolute;width:59px;height:16px;border-radius:3px;background:linear-gradient(var(--green-top),var(--green-bot));color:#fff;font-size:7px;font-weight:700;text-align:center;line-height:15px;border:1px solid #2c5a0a}
.card .btn-more{right:11px;bottom:12px}
.welcome-pic{left:104px;top:820px;width:197px;height:124px;border:2px solid #e2e2e2;
  background:linear-gradient(180deg,rgba(255,255,255,0) 55%,rgba(30,38,48,.35) 100%),
  linear-gradient(90deg,#eef2f5 0%,#dfe6eb 20%,#2c3540 40%,#3b4654 55%,#c9d2d9 62%,#232b35 75%,#eef2f5 100%)}
.welcome h2{position:absolute;left:318px;top:816px;font-size:17px;font-weight:500;color:var(--teal-dark)}
.welcome p{position:absolute;left:318px;top:842px;width:425px;font-size:8.4px;line-height:16px;color:var(--ink-soft)}
.clients{left:102px;top:960px;width:638px;height:88px;background:linear-gradient(#f2f2f2,#ffffff);border:1px solid #dcdcdc;box-shadow:0 2px 5px rgba(0,0,0,.2)}
.clients h2{position:absolute;left:14px;top:8px;font-size:16px;font-weight:500;color:var(--teal-dark)}
.client-row{position:absolute;left:14px;top:42px;width:606px;display:flex;justify-content:space-between;align-items:center;font-size:10.5px;font-weight:700;color:#39444a}
.client-row span{display:flex;align-items:center;gap:4px}
.client-row i{display:inline-block;width:9px;height:9px;background:#39444a}
.footer{left:0;top:1060px;width:847px;height:140px;background:var(--footer)}
.fcol{font-size:8.4px;line-height:19px;color:var(--footer-text)}
.fcol h3{font-size:12.5px;font-weight:500;color:#fff;margin-bottom:3px;line-height:18px}
.fcol h4{font-size:10px;font-weight:500;color:#fff;line-height:18px}
.badge{left:443px;top:1094px;width:132px;height:50px;border-radius:4px;background:#555}
.social{left:648px;top:1094px;display:flex;gap:7px}
.social i{width:20px;height:20px;border-radius:3px;background:#6f8f9a}
.flogo{left:620px;top:1125px;display:flex;align-items:center;gap:6px;color:#cfd3d4;font-weight:700;font-size:12px;letter-spacing:1px}
.flogo .mark{width:20px;height:20px;border-radius:50%;background:#9aa3a6}
.copy{left:657px;top:1174px;font-size:7px;color:#b0b0b0}
</style>
</head>
<body>
<header class="abs header">
  <div class="abs logo"><span class="mark"></span>CORVIN SOFTWARE</div>
  <div class="abs search">Search Keyword...<span class="btn"><svg width="13" height="13"><circle cx="8" cy="5" r="3.6" stroke="#1e2a20" stroke-width="1.8" fill="none"/><path d="M5.4 7.6 L1.5 11.5" stroke="#1e2a20" stroke-width="2.2"/></svg></span></div>
  <nav class="abs nav">
    <a href="#">Home</a><a href="#" class="active">Products</a><a href="#">Services</a><a href="#">News</a><a href="#">About Us</a><a href="#">Contact Us</a>
  </nav>
</header>

<section class="abs hero" role="img" aria-label="Oilfield pump jacks at dusk with two tablets showing the software dashboard">
  <h1>We Develop Software and Associated Services to some of the World’s Largest Oil Companies......</h1>
</section>
<div class="abs arrow" style="left:92px"><svg width="14" height="22"><path d="M12 1 L2 11 L12 21" stroke="#fff" stroke-width="2" fill="none"/></svg></div>
<div class="abs arrow" style="left:700px"><svg width="14" height="22"><path d="M2 1 L12 11 L2 21" stroke="#fff" stroke-width="2" fill="none"/></svg></div>
<ul class="abs dropdown"><li>TZQ</li><li>BLV</li><li>PNJ</li></ul>

<section class="abs news">
  <div class="label"><span class="ico" role="img" aria-label="Newspaper icon"></span>Latest News</div>
  <div class="body"><b>TZQ Selected by Aldera Gaswerk</b><i>Aldera Gaswerk E &amp; P GmbH has selected TZQ as the solution to provide probabilistic time and cost estimates for its drilling operations.</i></div>
  <div class="more">More News <span>›</span></div>
</section>

<section class="abs panel"></section>

<article class="abs card" style="left:104px;top:540px">
  <div class="pic" role="img" aria-label="Stopwatch illustration"></div>
  <h2>PLAN <span>( Time &amp; Cost Estimation )</span></h2>
  <p>TZQ delivers a standardized, systematic approach to understanding, quantifying and communicating the impact of project risk to all stakeholders.</p>
  <div class="btn-more">READ MORE</div>
</article>
<article class="abs card" style="left:430px;top:540px">
  <div class="pic" role="img" aria-label="Control gauge illustration"></div>
  <h2>EXECUTE <span>( Material &amp; Cost Control )</span></h2>
  <p>Since 1992 BLV has been helping companies optimize their materials and logistics processes and accurately track costs on a daily basis.</p>
  <div class="btn-more">READ MORE</div>
</article>
<article class="abs card" style="left:104px;top:665px">
  <div class="pic" role="img" aria-label="Chalkboard and books illustration"></div>
  <h2>LEARN <span>( Lessons Learned )</span></h2>
  <p>DrillSavant is an advanced lessons learned and knowledge management system for use in the Oil &amp; Gas industry. It’s fully searchable and easy to use.</p>
  <div class="btn-more">READ MORE</div>
</article>
<article class="abs card" style="left:430px;top:665px">
  <div class="pic" role="img" aria-label="Consultant with wrench illustration"></div>
  <h2>EMBED <span>( Services &amp; Consulting )</span></h2>
  <p>Software solutions rely on people and processes to deliver results. From analysis through execution we support our clients to improve performance.</p>
  <div class="btn-more">READ MORE</div>
</article>

<div class="abs welcome-pic" role="img" aria-label="Photo of two business professionals"></div>
<section class="welcome">
  <h2>Welcome to Our Site</h2>
  <p>Corvin Software have developed and continue to support software in over 30 countries, providing real results to hundreds of drilling operations.<br>With decades of hands-on software and well engineering experience, we are uniquely positioned to provide the right solution to our customers.</p>
  <div class="btn-more" style="left:318px;top:929px">READ MORE</div>
</section>

<section class="abs clients">
  <h2>Our Clients</h2>
  <div class="client-row">
    <span>DUNT</span><span><i></i>FALUMI</span><span>Marovel</span><span>VELO</span><span>Tolvan</span><span>Mersk Hollin</span><span>Paladex</span><span>Koruna</span><span>GN</span>
  </div>
</section>

<footer class="abs footer"></footer>
<div class="abs fcol" style="left:92px;top:1072px"><h3>Europe</h3>18 Corran Row<br>Dunmarrow, DM4 2QT<br>Phone:+44(0)1632 960417<br>Email:eu@corvinsoft.example</div>
<div class="abs fcol" style="left:258px;top:1072px"><h3>North America</h3>4100 Lakemont Pkwy, Suite 210<br>Brenford, TX 75099<br>Phone:(555) 014 2278<br>Email:us@corvinsoft.example</div>
<div class="abs fcol" style="left:438px;top:1071px"><h4>Featured Partners</h4></div>
<div class="abs badge" role="img" aria-label="Partner certification badge"></div>
<div class="abs fcol" style="left:648px;top:1071px"><h4>Follow us on</h4></div>
<div class="abs social" aria-label="Social links"><i></i><i></i><i></i><i></i></div>
<div class="abs flogo"><span class="mark"></span>CORVIN SOFTWARE</div>
<div class="abs copy">© 2013. All Right Reserved</div>
</body>
</html>
```